Business Cards for a law firm

Business cards for our law firm. Use our silhoette logo and OAK PARTNERS - check our website (www.oakpartners.example)

Contact Information for Business Card

our silhouette logo, OAK PARTNERS, 800-555-0147, Dorian Pemberton, dorian@oakpartners.example

Requirements
Must have
• our silhouette logo, OAK PARTNERS, 800-555-0147, Dorian Pemberton, dorian@oakpartners.example

```html
<!DOCTYPE html>
<html lang="en">
<head>
<meta charset="utf-8">
<title>Oak Partners – Business Cards</title>
<link rel="stylesheet" href="https://fonts.googleapis.com/css2?family=Cinzel:wght@500;600&family=Montserrat:wght@400;700&display=swap">
<style>
  :root {
    --navy: #223266;
    --navy-soft: #3a4a80;
    --white: #ffffff;
    --ink: #1f2a44;
    --backdrop: #8a7356;
    --card-shadow: rgba(0, 0, 0, 0.35);
  }
  html, body {
    margin: 0;
    padding: 0;
    width: 900px;
    height: 1200px;
    overflow: hidden;
  }
  body {
    position: relative;
    background: var(--backdrop);
    font-family: "Montserrat", Arial, sans-serif;
  }
  .card {
    position: absolute;
    border-radius: 22px;
    box-shadow: 0 6px 18px var(--card-shadow);
    overflow: hidden;
  }
  .card-front {
    left: 80px;
    top: 131px;
    width: 742px;
    height: 440px;
    background: var(--white);
  }
  .card-back {
    left: 78px;
    top: 638px;
    width: 744px;
    height: 440px;
    background: var(--navy);
  }
  .brand-mark-area {
    position: absolute;
    left: 10px;
    top: 32px;
    width: 275px;
    height: 408px;
    background: linear-gradient(180deg, rgba(34, 50, 102, 0.85), rgba(34, 50, 102, 0.95));
    border-radius: 4px;
  }
  .firm-name {
    font-family: "Cinzel", "Times New Roman", serif;
    font-weight: 600;
    letter-spacing: 0.06em;
    margin: 0;
    white-space: nowrap;
  }
  .card-front .firm-name {
    position: absolute;
    left: 363px;
    top: 80px;
    font-size: 29px;
    color: var(--navy);
  }
  .contact-block {
    position: absolute;
    left: 360px;
    top: 176px;
    color: var(--ink);
  }
  .person-name {
    margin: 0;
    font-weight: 700;
    font-size: 26px;
    color: var(--navy);
  }
  .person-role {
    margin: 2px 0 0;
    font-size: 16px;
  }
  .address {
    margin: 18px 0 0;
    font-size: 16px;
    line-height: 21px;
    font-style: normal;
  }
  .contact-list {
    list-style: none;
    margin: 16px 0 0;
    padding: 0;
    font-size: 16px;
  }
  .contact-list li {
    display: flex;
    align-items: center;
    gap: 9px;
    height: 28.5px;
  }
  .contact-list svg {
    width: 15px;
    height: 15px;
    fill: var(--navy);
    flex: none;
  }
  .back-brand {
    position: absolute;
    left: 76px;
    top: 182px;
    display: flex;
    align-items: center;
    gap: 22px;
  }
  .brand-dot {
    width: 62px;
    height: 62px;
    border-radius: 50%;
    background: var(--white);
  }
  .card-back .firm-name {
    font-size: 45px;
    color: var(--white);
  }
</style>
</head>
<body>
  <section class="card card-front" aria-label="Business card front">
    <div class="brand-mark-area" role="img" aria-label="Firm silhouette brand mark"></div>
    <h1 class="firm-name">OAK PARTNERS</h1>
    <div class="contact-block">
      <h2 class="person-name">Dorian Pemberton</h2>
      <p class="person-role">Lawyer</p>
      <address class="address">418 Linden Grove Ave, #210<br>Fairbrook, OH 430417</address>
      <ul class="contact-list">
        <li>
          <svg viewBox="0 0 24 24" aria-hidden="true"><path d="M6.6 10.8a15.1 15.1 0 0 0 6.6 6.6l2.2-2.2a1 1 0 0 1 1-.25 11.4 11.4 0 0 0 3.6.6 1 1 0 0 1 1 1V20a1 1 0 0 1-1 1A17 17 0 0 1 3 4a1 1 0 0 1 1-1h3.5a1 1 0 0 1 1 1c0 1.25.2 2.45.6 3.6a1 1 0 0 1-.25 1z"/></svg>
          <span>800-555-0147</span>
        </li>
        <li>
          <svg viewBox="0 0 24 24" aria-hidden="true"><path d="M2 5h20v2l-10 6L2 7zM2 9l10 6 10-6v10H2z"/></svg>
          <span>dorian@oakpartners.example</span>
        </li>
        <li>
          <svg viewBox="0 0 24 24" aria-hidden="true"><path d="M12 2a10 10 0 1 0 0 20 10 10 0 0 0 0-20zm-1 17.9A8 8 0 0 1 4.1 11H7v2l2 2v2l2 1zm6.9-2.6A2 2 0 0 0 16 16h-1v-3a1 1 0 0 0-1-1H8v-2h2a1 1 0 0 0 1-1V7h2a2 2 0 0 0 2-2v-.4a8 8 0 0 1 2.9 12.7z"/></svg>
          <span>www.oakpartners.example</span>
        </li>
      </ul>
    </div>
  </section>

  <section class="card card-back" aria-label="Business card back">
    <div class="back-brand">
      <span class="brand-dot" aria-hidden="true"></span>
      <h2 class="firm-name">OAK PARTNERS</h2>
    </div>
  </section>
</body>
</html>
```